New Business Card Design Project LORVANTI-Italy

we are LORVANTI-Italy
our company in the market for 3 years we are luxury cosmetic company and its about time for a facelift :)
i will like to have elegant luxurious and unique business card
that will give the person that get it a unique, luxurious and elegant impression
I'm VERY OPEN FOR NEW IDEAS , even duo i add a few files of things that i see on line and i like them

i add my logo as well
my website is LORVANTI.COM
(if you would like to see the main style that we have)

Target Market(s)

adult that have money :)

Industry/Entity Type

Business

Contact Information for Business Card

Name - Dario Lorvanti
Position - CEO and CO Founder
address - 4817 E Halvern
telephone - 555-384-1926
email - dario@lorvanti.com
fax - 555-384-1926
website - LORVANTI.COM

Colors
000000
959595
fbee3e
ffffff

Requirements
Must have
• big logo in GOLD color
• elegant look
• impressive
Nice to have
• not must but maybe classy pattern background
• not must but maybe emblem
• maybe clear plastic business card
Should not have
• colors
• images

```html
<!DOCTYPE html>
<html lang="en">
<head>
<meta charset="utf-8">
<title>LORVANTI Italy – Business Card</title>
<link href="https://fonts.googleapis.com/css2?family=Cinzel:wght@400;700&family=Open+Sans:wght@400&display=swap" rel="stylesheet">
<style>
  :root {
    --backdrop: #8f8f8f;
    --card-black: #0d0d0d;
    --card-sheen: #1c1c1c;
    --gold: #d9ac34;
    --gold-line: #b8902a;
    --grey-text: #b5b5b5;
    --white-text: #f2f2f2;
    --icon-glyph: #141414;
  }
  * { margin: 0; padding: 0; box-sizing: border-box; }
  html, body {
    width: 1200px;
    height: 900px;
    overflow: hidden;
    background: var(--backdrop);
  }
  .stage {
    position: relative;
    width: 1200px;
    height: 900px;
  }
  .card {
    position: absolute;
    top: 300px;
    width: 520px;
    height: 300px;
    border-radius: 22px;
    background:
      repeating-linear-gradient(90deg, rgba(255,255,255,0.015) 0 2px, transparent 2px 5px),
      linear-gradient(160deg, var(--card-sheen) 0%, var(--card-black) 55%, #050505 100%);
    box-shadow: 0 14px 30px rgba(0,0,0,0.35);
    overflow: hidden;
  }
  .card--front { left: 60px; }
  .card--back { left: 620px; }

  /* brand lockup */
  .brand {
    position: absolute;
    display: flex;
    flex-direction: column;
    align-items: center;
    font-family: "Cinzel", serif;
    font-weight: 400;
    color: var(--gold);
  }
  .brand__circle {
    width: 78px;
    height: 78px;
    border-radius: 50%;
    border: 3px solid var(--gold);
    margin-bottom: 14px;
  }
  .brand__name {
    font-size: 38px;
    line-height: 1;
    letter-spacing: 1px;
  }
  .brand__place {
    font-size: 15px;
    letter-spacing: 2px;
    margin-top: 6px;
  }
  .card--front .brand { left: 30px; top: 52px; width: 230px; }
  .card--back .brand { left: 0; top: 56px; width: 520px; }
  .card--back .brand__circle { width: 84px; height: 84px; }
  .card--back .brand__name { font-size: 40px; }

  .divider {
    position: absolute;
    left: 276px;
    top: 42px;
    width: 1px;
    height: 210px;
    background: var(--gold-line);
  }

  .person {
    position: absolute;
    left: 298px;
    top: 46px;
  }
  .person__name {
    font-family: "Cinzel", serif;
    font-weight: 700;
    font-size: 19px;
    color: var(--gold);
    letter-spacing: 0.5px;
  }
  .person__role {
    font-family: "Cinzel", serif;
    font-weight: 400;
    font-size: 13px;
    color: var(--grey-text);
    margin-top: 2px;
  }

  .contact-list {
    position: absolute;
    left: 298px;
    top: 112px;
    list-style: none;
    font-family: "Open Sans", sans-serif;
    font-size: 13px;
    color: var(--white-text);
  }
  .contact-list__item {
    display: flex;
    align-items: center;
    height: 23px;
  }
  .contact-list__icon {
    width: 15px;
    height: 15px;
    margin-right: 8px;
    flex: none;
  }
  .contact-list__item--address {
    margin-top: 10px;
  }
</style>
</head>
<body>
<main class="stage">

  <section class="card card--front" aria-label="Business card front">
    <div class="brand">
      <div class="brand__circle"></div>
      <div class="brand__name">LORVANTI</div>
      <div class="brand__place">ITALY</div>
    </div>

    <div class="divider"></div>

    <div class="person">
      <div class="person__name">DARIO LORVANTI</div>
      <div class="person__role">CEO and CO Founder</div>
    </div>

    <ul class="contact-list">
      <li class="contact-list__item">
        <svg class="contact-list__icon" viewBox="0 0 16 16" aria-hidden="true">
          <circle cx="8" cy="8" r="8" fill="var(--gold)"/>
          <path d="M5 4.5 L6.6 4.5 L7.2 6.3 L6.3 7 Q7 8.8 9 9.7 L9.7 8.8 L11.5 9.4 L11.5 11 Q7.5 11.5 5 7.5 Z" fill="var(--icon-glyph)"/>
        </svg>
        555-384-1926
      </li>
      <li class="contact-list__item">
        <svg class="contact-list__icon" viewBox="0 0 16 16" aria-hidden="true">
          <circle cx="8" cy="8" r="8" fill="var(--gold)"/>
          <rect x="5.5" y="4" width="5" height="3" fill="var(--icon-glyph)"/>
          <rect x="4" y="7.2" width="8" height="4.5" rx="0.8" fill="var(--icon-glyph)"/>
        </svg>
        555-384-1926
      </li>
      <li class="contact-list__item">
        <svg class="contact-list__icon" viewBox="0 0 16 16" aria-hidden="true">
          <circle cx="8" cy="8" r="8" fill="var(--gold)"/>
          <rect x="4" y="5" width="8" height="6" fill="var(--icon-glyph)"/>
          <path d="M4 5 L8 8.3 L12 5" fill="none" stroke="var(--gold)" stroke-width="0.9"/>
        </svg>
        dario@lorvanti.com
      </li>
      <li class="contact-list__item">
        <svg class="contact-list__icon" viewBox="0 0 16 16" aria-hidden="true">
          <circle cx="8" cy="8" r="8" fill="var(--gold)"/>
          <circle cx="8" cy="8" r="4" fill="none" stroke="var(--icon-glyph)" stroke-width="1.1"/>
          <path d="M4 8 H12 M8 4 Q5.8 8 8 12 Q10.2 8 8 4" fill="none" stroke="var(--icon-glyph)" stroke-width="0.9"/>
        </svg>
        LORVANTI.COM
      </li>
      <li class="contact-list__item contact-list__item--address">4817 E Halvern</li>
    </ul>
  </section>

  <section class="card card--back" aria-label="Business card back">
    <div class="brand">
      <div class="brand__circle"></div>
      <div class="brand__name">LORVANTI</div>
      <div class="brand__place">ITALY</div>
    </div>
  </section>

</main>
</body>
</html>
```